K & R Acre Works. Business card design

We need a business card designed for a new business. We have a bulldozer and tractor service. We clear land and make wildlife food plots. We provide disking, bush hogging, and site prep services.
I have attached an image of a business card that I like and would like my business cards to look similar.

Target Market(s)

anyone needing bulldozer and/or tractor services

Industry/Entity Type

Business

Contact Information for Business Card

K & R Acre Works, Operated by 7-T-Ranch
Wade Colton
601-472-3358
wcr4817@fieldmail-example.com

Font styles to use
Sans Serif

Colors

Designer to choose colors to be used in the design.

Requirements
Must have
• image of tractor and bulldozer
• Land Clearing
• Wildlife food plots
• Bush Hogging
• Disking
• Site prep
Nice to have
• i have included a image of a business card that i like. I would like mine to be similar.

```html
<!DOCTYPE html>
<html lang="en">
<head>
<meta charset="utf-8">
<title>K &amp; R Acre Works – Business Card</title>
<link rel="stylesheet" href="https://fonts.googleapis.com/css2?family=Roboto:wght@400;500;700&family=Roboto+Condensed:wght@700&display=swap">
<style>
  :root {
    --page-bg: #2b2b2b;
    --band-olive: #9b9a3c;
    --text-light: #ffffff;
    --brand-brown: #7a3d0c;
    --tagline-dark: #3a3a3a;
    --photo-green: #5f7a4a;
    --photo-yellow: #c9c24a;
    --photo-orange: #d8623a;
  }
  * { box-sizing: border-box; margin: 0; padding: 0; }
  html, body {
    width: 1200px; height: 960px; overflow: hidden;
    background: var(--page-bg);
    font-family: "Roboto", Arial, sans-serif;
  }
  .business-card {
    position: absolute; left: 300px; top: 310px;
    width: 600px; height: 342px;
    overflow: hidden;
  }
  .equipment-photo {
    position: absolute; left: 0; top: 0; width: 600px; height: 207px;
    background:
      linear-gradient(90deg, var(--photo-yellow) 0%, #8c9a5a 30%, var(--photo-green) 52%, #8a6a4a 62%, var(--photo-orange) 78%, #c96a4a 100%);
  }
  .equipment-photo::after {
    content: ""; position: absolute; inset: 0;
    background: linear-gradient(180deg, rgba(120,150,110,0.55) 0%, rgba(255,255,255,0) 45%, rgba(60,60,40,0.15) 100%);
  }
  .brand-lockup {
    position: absolute; left: 114px; top: 74px; z-index: 2;
    display: flex; flex-direction: column; align-items: flex-start;
  }
  .brand-name {
    display: flex; align-items: center; gap: 8px;
    font-family: "Roboto Condensed", Arial, sans-serif;
    font-weight: 700; font-size: 30px; letter-spacing: 0.5px;
    color: var(--brand-brown); text-transform: uppercase; line-height: 1;
  }
  .brand-mark { width: 26px; height: 26px; background: var(--brand-brown); }
  .brand-tagline {
    margin-top: 6px;
    font-family: "Roboto Condensed", Arial, sans-serif;
    font-weight: 700; font-size: 15px; color: var(--tagline-dark);
    text-transform: uppercase; letter-spacing: 0.2px;
  }
  .info-band {
    position: absolute; left: 0; top: 207px; width: 600px; height: 135px;
    background: var(--band-olive); color: var(--text-light);
  }
  .services { position: absolute; left: 27px; top: 18px; }
  .services-title { font-weight: 700; font-size: 16px; margin-bottom: 6px; }
  .services-list { list-style: none; font-size: 14px; line-height: 18px; }
  .services-list li::before { content: "•"; margin-right: 6px; }
  .services-list .inline-dot { margin: 0 3px; }
  .contact { position: absolute; right: 27px; top: 12px; text-align: right; }
  .contact-name {
    font-family: "Roboto Condensed", Arial, sans-serif;
    font-weight: 700; font-size: 21px; text-transform: uppercase; line-height: 1.1;
  }
  .contact-role { font-size: 15px; text-transform: uppercase; margin-bottom: 10px; }
  .contact-line {
    display: flex; justify-content: flex-end; align-items: center; gap: 7px;
    font-size: 14px; line-height: 18px;
  }
  .contact-line svg { width: 13px; height: 13px; fill: var(--text-light); }
</style>
</head>
<body>
  <section class="business-card">
    <div class="equipment-photo" role="img" aria-label="Photo of a yellow bulldozer and an orange tractor working on cleared land"></div>
    <div class="brand-lockup">
      <div class="brand-name"><span class="brand-mark"></span>K &amp; R Acre Works</div>
      <div class="brand-tagline">For all of your land improvement needs</div>
    </div>
    <div class="info-band">
      <div class="services">
        <h2 class="services-title">WE CREADED</h2>
        <ul class="services-list">
          <li>Land Clearing</li>
          <li>Wildlife food plots</li>
          <li>Bush Hogging</li>
          <li>Disking<span class="inline-dot">•</span>Site prep</li>
        </ul>
      </div>
      <div class="contact">
        <div class="contact-name">Wade Colton</div>
        <div class="contact-role">Owner</div>
        <div class="contact-line">601-472-3358
          <svg viewBox="0 0 24 24" aria-hidden="true"><path d="M6.6 10.8a15.1 15.1 0 0 0 6.6 6.6l2.2-2.2a1 1 0 0 1 1-.25 11.4 11.4 0 0 0 3.6.57 1 1 0 0 1 1 1V20a1 1 0 0 1-1 1A17 17 0 0 1 3 4a1 1 0 0 1 1-1h3.5a1 1 0 0 1 1 1c0 1.25.2 2.45.57 3.57a1 1 0 0 1-.25 1z"/></svg>
        </div>
        <div class="contact-line">wcr4817@fieldmail-example.com
          <svg viewBox="0 0 24 24" aria-hidden="true"><path d="M2 5h20v14H2z M3.5 6.5 12 13l8.5-6.5" fill="none" stroke="#fff" stroke-width="2"/></svg>
        </div>
        <div class="contact-line">kracreworks-example.com
          <svg viewBox="0 0 24 24" aria-hidden="true"><circle cx="12" cy="12" r="10"/><path d="M2 12h20M12 2c3 3 3 17 0 20M12 2c-3 3-3 17 0 20" fill="none" stroke="#9b9a3c" stroke-width="1.6"/></svg>
        </div>
      </div>
    </div>
  </section>
</body>
</html>
```